At Home Pet Euthanasia - business cards & brand stationary

We already have a logo and the colors and a website. Need a business card designed that will be able to customized to multiple veterinarians who will be partnering with us. The feel needs to be compassionate, comforting with our tagline 'A Gift of Love at Home'. It will be 2 sides.
On the back our platform/partner vets will be customizing each business card with their own service areas, phone numbers, name and title. On the front, i would like to see experimentation with use of our photos, the logo, tagline and a description 'Peaceful and Compassionate At-Home Pet Euthanasia'

```html
<!DOCTYPE html>
<html lang="en">
<head>
<meta charset="utf-8">
<title>HearthPaw Business Card</title>
<link rel="stylesheet" href="https://fonts.googleapis.com/css2?family=Questrial&family=Dancing+Script:wght@600&display=swap">
<style>
  :root {
    --brand-blue: #7598c4;
    --ink: #5a5a5a;
    --card-white: #ffffff;
    --backdrop: #7c7c7c;
    --photo-warm: #d9b8a6;
    --photo-cool: #cfd2d6;
  }
  * { margin: 0; padding: 0; box-sizing: border-box; }
  html, body { width: 1133px; height: 1200px; overflow: hidden; }
  body {
    background: var(--backdrop);
    font-family: "Questrial", sans-serif;
    position: relative;
  }
  .card {
    position: absolute;
    left: 200px;
    width: 722px;
    height: 412px;
    background: var(--card-white);
    overflow: hidden;
  }
  .card--front { top: 144px; }
  .card--back { top: 641px; }

  /* Front */
  .brand {
    position: absolute;
    left: 86px;
    top: 170px;
    display: flex;
    align-items: center;
    gap: 12px;
  }
  .brand__mark {
    width: 40px;
    height: 40px;
    background: var(--brand-blue);
  }
  .brand__name {
    color: var(--brand-blue);
    font-size: 48px;
    line-height: 1;
  }
  .brand__tagline {
    position: absolute;
    left: 186px;
    top: 236px;
    color: var(--brand-blue);
    font-size: 17px;
    font-style: italic;
  }
  .divider {
    position: absolute;
    left: 397px;
    top: 115px;
    width: 1px;
    height: 181px;
    background: var(--ink);
    opacity: 0.6;
  }
  .contact {
    position: absolute;
    left: 419px;
    top: 112px;
    color: var(--ink);
    font-size: 16px;
    line-height: 20px;
  }
  .contact__name {
    color: var(--brand-blue);
    font-size: 23px;
    letter-spacing: 0.5px;
    line-height: 28px;
    font-weight: 700;
  }
  .contact__title { margin-bottom: 16px; }
  .contact__address { margin-bottom: 13px; }
  .contact__line { display: flex; align-items: center; gap: 9px; }
  .contact__icon { width: 14px; height: 14px; fill: var(--brand-blue); flex: none; }
  .card__band {
    position: absolute;
    left: 0;
    bottom: 0;
    width: 100%;
    height: 15px;
    background: var(--brand-blue);
  }

  /* Back */
  .photo {
    position: absolute;
    inset: 0;
    background: linear-gradient(100deg, var(--photo-warm) 0%, #e6cfc2 40%, #e8e3dc 60%, var(--photo-cool) 100%);
  }
  .description {
    position: absolute;
    left: 0;
    top: 340px;
    width: 100%;
    height: 43px;
    background: var(--brand-blue);
    color: var(--card-white);
    font-family: "Dancing Script", cursive;
    font-weight: 600;
    font-size: 27px;
    display: flex;
    align-items: center;
    justify-content: center;
  }
</style>
</head>
<body>
  <section class="card card--front">
    <div class="brand">
      <span class="brand__mark"></span>
      <span class="brand__name">HearthPaw</span>
    </div>
    <p class="brand__tagline">A gift of love at home.</p>
    <div class="divider"></div>
    <div class="contact">
      <p class="contact__name">DANIEL REYES</p>
      <p class="contact__title">President</p>
      <p class="contact__address">4120 Willow Bend Road<br>Juneau, Alaska 99801</p>
      <p class="contact__line">
        <svg class="contact__icon" viewBox="0 0 24 24"><path d="M6.6 10.8a15 15 0 0 0 6.6 6.6l2.2-2.2a1 1 0 0 1 1-.25 11.4 11.4 0 0 0 3.6.57 1 1 0 0 1 1 1V20a1 1 0 0 1-1 1A17 17 0 0 1 3 4a1 1 0 0 1 1-1h3.5a1 1 0 0 1 1 1c0 1.25.2 2.45.57 3.57a1 1 0 0 1-.25 1z"/></svg>
        555-214-7730
      </p>
      <p class="contact__line">
        <svg class="contact__icon" viewBox="0 0 24 24"><path d="M2 5h20v14H2z M2 5l10 7 10-7" stroke="#fff" stroke-width="1.5"/></svg>
        daniel@hearthpaw.com
      </p>
      <p class="contact__line">
        <svg class="contact__icon" viewBox="0 0 24 24"><circle cx="12" cy="12" r="10"/></svg>
        www.hearthpaw.com
      </p>
    </div>
    <div class="card__band"></div>
  </section>

  <section class="card card--back">
    <div class="photo" role="img" aria-label="Photo of a young girl kissing a blue-eyed tabby cat she holds in her arms"></div>
    <p class="description">Peaceful &amp; Compassionate At-Home Pet Euthanasia</p>
  </section>
</body>
</html>
```